New Company Logo & Responsive Website Design for Codeworks Heron

Codeworks Heron provides a white labeled, digital lending platform technology solutions to the mortgage industry via a SaaS model. Our target market is Mortgage Companies and Banks who are looking for innovative technology to assist both borrowers and loan originators with the lending process, while automating as much of he process as possible.

Codeworks Heron is our company name, and our modular software offerings Include the following Products:

1) Applicant Heron: A customizable, web based, point-of-sale application for borrowers to complete a loan application, and guide them through the mortgage process.

POS Definition
"A point of sale (POS) is the client-facing software solution that allows borrowers to create a customer portal, apply for a loan online, and seamlessly submit needed documentation."

2) Ledger Heron: A Mortgage Loan Origination System

LOS Definition
"A Mortgage Loan Origination System (LOS) is a platform that takes a completed loan application and facilitates the mortgage transaction from origination to post closing. LOS systems may include document management, pricing and eligibility engines, and compliance tools to decrease risk and increase loan manufacturing quality.

3) Dwelling Heron: A brandable, home search website

The LOS and POS definitions provided above are just for your understanding of what these products are, not to be included word-for-word as website content.

We are looking for designs that are elegant, convey technical competency, simple to navigate, and set us apart from the competition.

We are not set on any particular colors at this point, so feel free to choose the best colors for your particular designs.

Please include company logo, both desktop and mobile designs with a template design for the website sub pages.

Some Examples of Mortgage Technology Websites offering similar products. These are to show the typical content, not designs that we particularly like or dislike.

https://brantiq.example/
https://www.clearvantro.example/
https://www.abodefundbuddy.example/
https://www.debtquokka.example/
https://www.ternixapps.example/products/trail

Please send comments with additional questions.

Thank You For your participation.

Mortgage Companies

```html
<!DOCTYPE html>
<html lang="en">
<head>
<meta charset="utf-8">
<title>Codeworks Heron</title>
<link rel="stylesheet" href="https://fonts.googleapis.com/css2?family=Montserrat:wght@500;600;700;800&family=Lato:wght@400;700&display=swap">
<style>
:root{
  --blue:#1f73c4;
  --blue-dark:#165ea3;
  --ink:#1b1b1b;
  --text:#3a3a3a;
  --muted:#555;
  --line:#e6e9ee;
  --footer:#0b0b0b;
  --white:#fff;
}
*{box-sizing:border-box;margin:0;padding:0}
html,body{width:1200px;height:3290px;overflow:hidden}
body{position:relative;background:var(--white);font-family:'Lato',sans-serif;color:var(--text)}
.abs{position:absolute}
.brand{font-family:'Montserrat',sans-serif;font-weight:700;font-size:24px;color:var(--ink);letter-spacing:.2px;white-space:nowrap}
.brand.light{color:var(--white)}
.heading{font-family:'Montserrat',sans-serif;font-weight:700;font-size:30px;color:var(--ink);letter-spacing:.5px}
.heading span{color:var(--blue)}
.btn{position:absolute;display:flex;align-items:center;justify-content:center;background:var(--blue);color:var(--white);font-family:'Montserrat',sans-serif;font-weight:700;font-size:15px;border-radius:5px}
.btn.outline{background:transparent;color:var(--blue);border:2px solid var(--blue)}
.para{font-size:15.5px;line-height:25.7px;text-align:justify;color:var(--text)}

.site-header{position:absolute;left:0;top:0;width:1200px;height:98px;border-bottom:1px solid var(--line)}
.nav{position:absolute;top:38px;font-family:'Montserrat',sans-serif;font-weight:500;font-size:15px;color:var(--ink)}

.hero{position:absolute;left:0;top:98px;width:1200px;height:465px;background:radial-gradient(ellipse at 10% 90%,#dbe8f6 0%,rgba(255,255,255,0) 55%),linear-gradient(90deg,#f3f7fc,#fff 60%)}
.hero .arrow{position:absolute;top:212px}
.hero-title{position:absolute;left:110px;top:146px;font-family:'Montserrat',sans-serif;font-weight:800;font-size:37px;color:var(--blue);white-space:nowrap;letter-spacing:.2px}

.about{position:absolute;left:0;top:616px;width:1200px;height:514px;background:linear-gradient(90deg,#e2e6ec,#eef0f3 55%,#dfe4ea)}

.card{position:absolute;top:1307px;width:310px;height:341px;background:var(--white);box-shadow:0 4px 18px rgba(30,50,80,.10);text-align:center}
.card .icon{position:absolute;left:92px;top:33px;width:126px;height:126px;border-radius:50%;background:var(--white);box-shadow:0 3px 12px rgba(30,50,80,.14);display:flex;align-items:center;justify-content:center}
.card .icon.active{background:var(--blue)}
.card h3{position:absolute;top:187px;width:100%;font-family:'Montserrat',sans-serif;font-weight:500;font-size:20px;color:var(--ink)}
.card p{position:absolute;top:231px;width:100%;font-size:13.5px;color:var(--text)}
.card .more{position:absolute;top:278px;width:100%;font-family:'Montserrat',sans-serif;font-weight:600;font-size:15px;color:var(--blue)}

.testimonials{position:absolute;left:0;top:1736px;width:1200px;height:600px;background:linear-gradient(120deg,#eaf0f8,#dfe8f4 50%,#e9eff7)}
.quote{position:absolute;width:78px;height:78px;border-radius:50%;background:var(--blue);display:flex;align-items:center;justify-content:center}
.testi-text{position:absolute;width:380px;font-size:14.5px;line-height:25.7px;text-align:justify;color:var(--muted)}
.avatar{position:absolute;width:82px;height:82px;border-radius:50%;background:linear-gradient(160deg,#c9cdd3,#5a6270)}
.t-name{position:absolute;font-family:'Montserrat',sans-serif;font-weight:500;font-size:20px;color:var(--blue)}
.t-role{position:absolute;font-size:14px;color:var(--text)}
.dot{position:absolute;top:2260px;width:11px;height:11px;border-radius:50%;background:#c3cbd6}
.dot.on{background:var(--blue)}

.logo-tile{position:absolute;background:var(--white);box-shadow:0 3px 14px rgba(30,50,80,.14);border-radius:3px}
.logo-tile .mark{position:absolute;left:20%;top:28%;width:60%;height:44%;border-radius:4px}

.site-footer{position:absolute;left:0;top:2886px;width:1200px;height:404px;background:var(--footer);color:var(--white)}
.f-head{position:absolute;top:2958px;font-family:'Montserrat',sans-serif;font-weight:600;font-size:19px;color:var(--white)}
.f-link{position:absolute;font-size:14.5px;line-height:18px;color:var(--white)}
.social{position:absolute;top:3120px;width:42px;height:42px;border-radius:50%;background:var(--white)}
</style>
</head>
<body>

<header class="site-header">
  <div class="abs brand" style="left:110px;top:34px">CODEWORKS <span style="color:var(--blue)">HERON</span></div>
  <nav>
    <span class="nav" style="left:444px">Home</span>
    <span class="nav" style="left:520px">About</span>
    <span class="nav" style="left:596px">How It Work</span>
    <span class="nav" style="left:715px">Mortgage Blog</span>
    <span class="nav" style="left:852px">Contact</span>
  </nav>
  <div class="btn" style="left:973px;top:22px;width:115px;height:54px">LOG IN</div>
</header>

<section class="hero">
  <svg class="arrow" style="left:52px" width="20" height="34" viewBox="0 0 20 34"><path d="M17 3 3 17l14 14" fill="none" stroke="#1f73c4" stroke-width="3.5" stroke-linecap="round"/></svg>
  <svg class="arrow" style="left:1120px" width="20" height="34" viewBox="0 0 20 34"><path d="M3 3l14 14L3 31" fill="none" stroke="#aab4c0" stroke-width="3" stroke-linecap="round"/></svg>
  <div class="abs" style="left:111px;top:92px;font-family:'Montserrat',sans-serif;font-weight:500;font-size:30px;color:var(--ink)">WELCOME TO</div>
  <div class="hero-title">CODEWORKS HERON</div>
  <p class="abs" style="left:111px;top:210px;width:440px;font-size:15px;line-height:25.7px">Lorem ipsum dolor sit amet, consectetur adipiscing elit, sed do eiusmod tempor incididunt ut labore et dolore magna aliqua.</p>
  <div class="btn outline" style="left:111px;top:286px;width:167px;height:53px">REQUEST DEMO</div>
  <div class="abs" role="img" aria-label="Laptop showing the lending dashboard with charts" style="left:638px;top:84px;width:446px;height:296px;border-radius:12px;background:linear-gradient(160deg,#f7f9fc,#e6ecf4);box-shadow:0 6px 20px rgba(30,50,80,.12)"></div>
  <div class="abs" role="img" aria-label="Phone showing the statistics screen" style="left:580px;top:146px;width:132px;height:270px;border-radius:16px;background:linear-gradient(180deg,#f4f6fb,#dfe3f2 60%,#c9cbe8);box-shadow:0 8px 24px rgba(60,60,140,.2)"></div>
</section>

<section class="about">
  <svg class="abs" style="left:130px;top:50px" width="420" height="420" viewBox="0 0 420 420"><circle cx="210" cy="210" r="207" fill="none" stroke="#3f86cc" stroke-width="2"/></svg>
  <div class="abs" role="img" aria-label="Modern house at dusk" style="left:169px;top:86px;width:342px;height:342px;border-radius:50%;background:linear-gradient(180deg,#3c6fb6 0%,#6d8fbf 45%,#8a7a62 70%,#4a4f55 100%)"></div>
  <h2 class="abs heading" style="left:624px;top:88px">ABOUT <span>US</span></h2>
  <p class="abs para" style="left:624px;top:152px;width:463px">Lorem ipsum dolor sit amet, consectetur adipiscing elit, sed do eiusmod tempor incididunt ut labore et dolore magna aliqua. Ut enim ad minim veniam, quis nostrud exercitation ullamco laboris nisi ut aliquip ex ea commodo consequat. Duis aute irure dolor in reprehenderit in voluptate velit esse cillum dolore eu fugiat nulla pariatur. Excepteur sint occaecat cupidatat non proident, sunt in culpa qui officia deserunt mollit anim id est laborum.</p>
  <div class="btn" style="left:624px;top:366px;width:155px;height:53px">LEARN MORE</div>
</section>

<section class="services">
  <h2 class="abs heading" style="left:0;top:1210px;width:1200px;text-align:center">OUR <span>SERVICES</span></h2>

  <div class="card" style="left:111px">
    <div class="icon"><svg width="56" height="56" viewBox="0 0 56 56" fill="none" stroke="#1f73c4" stroke-width="2"><circle cx="28" cy="16" r="9"/><path d="M28 11v10M25 13h5a2 2 0 0 1 0 4h-4a2 2 0 0 0 0 4h5"/><path d="M6 38h8l8-4h10a3 3 0 0 1 0 6H22"/><path d="M14 48h18l14-9a3 3 0 0 0-3-5l-11 6"/><rect x="2" y="36" width="6" height="14"/></svg></div>
    <h3>Applicant Heron</h3>
    <p>A customizable, web based, point-of-sale</p>
    <div class="more">Learn More &rarr;</div>
  </div>

  <div class="card" style="left:445px">
    <div class="icon active"><svg width="60" height="60" viewBox="0 0 60 60" fill="none" stroke="#fff" stroke-width="2.2"><path d="M6 28 28 10l22 18"/><path d="M12 24v26h18"/><rect x="18" y="32" width="8" height="8"/><circle cx="42" cy="42" r="10"/><path d="M42 36v12M39 38.5h4.5a1.8 1.8 0 0 1 0 3.5h-3a1.8 1.8 0 0 0 0 3.5H45"/></svg></div>
    <h3>Ledger Heron</h3>
    <p>A Mortgage Loan Origination System</p>
    <div class="more">Learn More &rarr;</div>
  </div>

  <div class="card" style="left:779px">
    <div class="icon"><svg width="58" height="58" viewBox="0 0 58 58" fill="none" stroke="#1f73c4" stroke-width="2.2"><path d="M4 28 29 7l25 21"/><path d="M10 23v28h38V23"/><rect x="20" y="28" width="18" height="16"/><path d="M29 28v16M20 36h18"/><path d="M6 51h46"/></svg></div>
    <h3>Dwelling Heron</h3>
    <p>A brandable, home search website</p>
    <div class="more">Learn More &rarr;</div>
  </div>
</section>

<section class="testimonials">
  <h2 class="abs heading" style="left:0;top:72px;width:1200px;text-align:center">OUR <span>TESTIMONIALS</span></h2>
</section>
<div class="quote" style="left:112px;top:1874px"><svg width="40" height="30" viewBox="0 0 40 30" fill="#fff"><path d="M0 30V17C0 7 5 1 15 0v6c-5 1-7 4-7 9h7v15zM22 30V17C22 7 27 1 37 0v6c-5 1-7 4-7 9h7v15z"/></svg></div>
<p class="testi-text" style="left:173px;top:1922px">Lorem ipsum dolor sit amet, consectetur adipiscing elit, sed do eiusmod tempor incididunt ut labore et dolore magna aliqua. Ut enim ad minim veniam, quis nostrud exercitation ullamco laboris nisi ut aliquip ex ea commodo consequat. Duis aute irure dolor in reprehenderit in voluptate velit esse cillum dolore eu fugiat nulla pariatur. Excepteur sint occaecat cupidatat non proident, sunt in culpa qui officia deserunt mollit anim id est laborum.</p>
<div class="avatar" role="img" aria-label="Portrait of the client" style="left:173px;top:2149px"></div>
<div class="t-name" style="left:281px;top:2164px">Marcus Dale</div>
<div class="t-role" style="left:281px;top:2196px">Lorem ipsum dolor sit</div>

<div class="quote" style="left:645px;top:1874px"><svg width="40" height="30" viewBox="0 0 40 30" fill="#fff"><path d="M0 30V17C0 7 5 1 15 0v6c-5 1-7 4-7 9h7v15zM22 30V17C22 7 27 1 37 0v6c-5 1-7 4-7 9h7v15z"/></svg></div>
<p class="testi-text" style="left:706px;top:1922px">Lorem ipsum dolor sit amet, consectetur adipiscing elit, sed do eiusmod tempor incididunt ut labore et dolore magna aliqua. Ut enim ad minim veniam, quis nostrud exercitation ullamco laboris nisi ut aliquip ex ea commodo consequat. Duis aute irure dolor in reprehenderit in voluptate velit esse cillum dolore eu fugiat nulla pariatur. Excepteur sint occaecat cupidatat non proident, sunt in culpa qui officia deserunt mollit anim id est laborum.</p>
<div class="avatar" role="img" aria-label="Portrait of the client" style="left:706px;top:2149px"></div>
<div class="t-name" style="left:814px;top:2164px">Marcus Dale</div>
<div class="t-role" style="left:814px;top:2196px">Lorem ipsum dolor sit</div>

<span class="dot" style="left:566px"></span>
<span class="dot on" style="left:585px"></span>
<span class="dot" style="left:604px"></span>
<span class="dot" style="left:623px"></span>

<section class="productivity">
  <h2 class="abs heading" style="left:114px;top:2418px">PRODUCTIVITY <span>SOLUTIONS</span></h2>
  <p class="abs para" style="left:113px;top:2480px;width:463px">Lorem ipsum dolor sit amet, consectetur adipiscing elit, sed do eiusmod tempor incididunt ut labore et dolore magna aliqua. Ut enim ad minim veniam, quis nostrud exercitation ullamco laboris nisi ut aliquip ex ea commodo consequat. Duis aute irure dolor in reprehenderit in voluptate velit esse cillum dolore eu fugiat nulla pariatur. Excepteur sint occaecat cupidatat non proident, sunt in culpa qui officia deserunt mollit anim id est laborum.</p>
  <div class="btn" style="left:113px;top:2694px;width:155px;height:53px">LEARN MORE</div>

  <div class="logo-tile" style="left:822px;top:2430px;width:180px;height:190px"></div>
  <div class="logo-tile" style="left:697px;top:2455px;width:165px;height:160px"></div>
  <div class="logo-tile" role="img" aria-label="Sample client logo" style="left:655px;top:2424px;width:166px;height:142px"><div class="mark" style="background:#dbe9f6"></div></div>
  <div class="logo-tile" role="img" aria-label="Sample client logo" style="left:889px;top:2452px;width:168px;height:166px"><div class="mark" style="background:#e2eaf3"></div></div>
  <div class="logo-tile" role="img" aria-label="Sample client logo" style="left:703px;top:2566px;width:218px;height:218px"><div class="mark" style="background:#dfe6f3"></div></div>
</section>

<footer class="site-footer"></footer>
<div class="abs brand light" style="left:110px;top:3036px">CODEWORKS <span style="color:var(--blue)">HERON</span></div>
<span class="social" aria-label="Social link" style="left:112px"></span>
<span class="social" aria-label="Social link" style="left:166px"></span>
<span class="social" aria-label="Social link" style="left:221px"></span>
<span class="social" aria-label="Social link" style="left:275px"></span>

<div class="f-head" style="left:418px">QUICK LINKS</div>
<a class="f-link" style="left:418px;top:3006px">Home</a>
<a class="f-link" style="left:418px;top:3032px">About</a>
<a class="f-link" style="left:418px;top:3058px">How It Work</a>
<a class="f-link" style="left:418px;top:3083px">Mortgage Blog</a>
<a class="f-link" style="left:418px;top:3109px">Contact</a>

<div class="f-head" style="left:620px">CONTACT US</div>
<svg class="abs" style="left:620px;top:3014px" width="16" height="22" viewBox="0 0 16 22"><path d="M8 0a8 8 0 0 0-8 8c0 6 8 14 8 14s8-8 8-14a8 8 0 0 0-8-8zm0 11a3 3 0 1 1 0-6 3 3 0 0 1 0 6z" fill="#fff"/></svg>
<div class="f-link" style="left:651px;top:3014px;line-height:25.7px">Lorem ipsum dolor sit<br>amet, consectetur</div>
<svg class="abs" style="left:620px;top:3080px" width="18" height="18" viewBox="0 0 24 24"><path d="M6.6 10.8a15 15 0 0 0 6.6 6.6l2.2-2.2a1 1 0 0 1 1-.25 11.4 11.4 0 0 0 3.6.6 1 1 0 0 1 1 1V20a1 1 0 0 1-1 1A17 17 0 0 1 3 4a1 1 0 0 1 1-1h3.5a1 1 0 0 1 1 1 11.4 11.4 0 0 0 .6 3.6 1 1 0 0 1-.25 1z" fill="#fff"/></svg>
<div class="f-link" style="left:651px;top:3081px">+1 (555) 014 2290</div>
<svg class="abs" style="left:620px;top:3117px" width="18" height="14" viewBox="0 0 18 14"><rect width="18" height="14" rx="1.5" fill="#fff"/><path d="M1 1.5 9 8l8-6.5" fill="none" stroke="#0b0b0b" stroke-width="1.6"/></svg>
<div class="f-link" style="left:651px;top:3115px">info@codeworksheron.example</div>

<div class="f-head" style="left:864px">NEWSLETTER</div>
<div class="abs" style="left:864px;top:3012px;width:224px;height:40px;background:#fff;border-radius:4px"></div>
<div class="abs" style="left:878px;top:3024px;font-size:14px;color:#888">Enter email</div>
<div class="btn" style="left:1035px;top:3012px;width:53px;height:40px;border-radius:4px"><svg width="16" height="12" viewBox="0 0 18 14"><rect width="18" height="14" rx="1.5" fill="#fff"/><path d="M1 1.5 9 8l8-6.5" fill="none" stroke="#1f73c4" stroke-width="1.6"/></svg></div>

<div class="abs" style="left:420px;top:3226px;font-size:14px;color:#fff">&copy;Copyrights 2022 Codeworks Heron &nbsp;| &nbsp; All Rights Reserved</div>

</body>
</html>
```